Morvane Business Card

We need a business card design for Morvane, an independent sewing pattern company based near Quebec City. We make patterns for children and adults and specialize in everything other big pattern brands won't tackle: activewear, sportswear (figure skating, gymnastics), underwear. We are a small business and would like our cards to be stylish and fun, not corporate looking.

Target Market(s)

Educated women 35-55 who sew for themselves or their family. They like fashion and sew to be different and make clothes that fit them like a glove, not necessarily to save money.

Industry/Entity Type

Small Business

Requirements
Must have
• Morvane logo, contact info:

Claire Dufresne, president & founder / présidente et fondatrice

Morvane
3156 rue Tessier
Ste-Odile QC H2K4P9
Canada

info@morvane.com
www.morvane.com
Nice to have
• Sewing/fashion-related graphics. You can use any pattern cover available on www.morvane.com for inspiration. Stylish illustrations / sketches inspired by existing garments we have would be great. Something showing pattern grading could also be an option.

The design can be on one- or two-sided. We are open to variations (e.g. 4-5 different backs for a given card)
Should not have
• nothing too cartoonish or girly please :) we prefer something timeless, fashion-forward.

```html
<!DOCTYPE html>
<html lang="en">
<head>
<meta charset="utf-8">
<title>Morvane Business Card</title>
<link rel="stylesheet" href="https://fonts.googleapis.com/css2?family=Comfortaa:wght@400;600;700&display=swap">
<style>
  :root {
    --card-pink: #d5127b;
    --card-pink-dark: #b80e6a;
    --ink: #1c0812;
    --stitch-white: #ffffff;
    --art-tone: #2a0418;
  }
  html, body {
    margin: 0;
    padding: 0;
    width: 1200px;
    height: 699px;
    overflow: hidden;
  }
  .card {
    position: relative;
    width: 1200px;
    height: 699px;
    overflow: hidden;
    background-color: var(--card-pink);
    background-image:
      repeating-linear-gradient(0deg, rgba(0,0,0,0.04) 0 2px, transparent 2px 5px),
      repeating-linear-gradient(90deg, rgba(255,255,255,0.03) 0 2px, transparent 2px 6px);
    font-family: "Comfortaa", sans-serif;
  }
  .corner-frame {
    position: absolute;
    width: 230px;
    height: 212px;
  }
  .corner-frame--top-left { left: 8px; top: 8px; }
  .corner-frame--bottom-right { left: 963px; top: 478px; }
  .corner-frame__fill { fill: var(--card-pink-dark); }
  .corner-frame__line {
    fill: none;
    stroke: var(--ink);
    stroke-width: 3;
  }
  .dress-form {
    position: absolute;
    left: 153px;
    top: 48px;
    width: 258px;
    height: 651px;
    border-radius: 90px 90px 30px 30px;
    background: linear-gradient(180deg, var(--art-tone) 0%, #5a0a36 55%, var(--card-pink-dark) 100%);
  }
  .contact {
    position: absolute;
    left: 470px;
    top: 222px;
    width: 640px;
    text-align: center;
    color: var(--ink);
  }
  .contact__name {
    margin: 0;
    font-size: 70px;
    font-weight: 600;
    letter-spacing: 3px;
    line-height: 74px;
    color: var(--stitch-white);
  }
  .contact__role {
    margin: 2px 0 0;
    font-size: 37px;
    font-weight: 600;
    letter-spacing: 3px;
    line-height: 44px;
  }
  .contact__links {
    margin: 56px 0 0;
    font-size: 35px;
    font-weight: 600;
    letter-spacing: 1px;
    line-height: 52px;
  }
</style>
</head>
<body>
  <main class="card">
    <svg class="corner-frame corner-frame--top-left" viewBox="0 0 230 212" role="img" aria-label="Scrolled corner ornament">
      <polygon class="corner-frame__fill" points="10,10 200,10 10,190"/>
      <polygon class="corner-frame__line" points="2,2 228,2 2,210"/>
      <polygon class="corner-frame__line" points="10,10 200,10 10,190"/>
    </svg>

    <div class="dress-form" role="img" aria-label="Black wire dress form mannequin silhouette"></div>

    <section class="contact">
      <h1 class="contact__name">Claire Dufresne</h1>
      <p class="contact__role">president &amp; founder</p>
      <p class="contact__links">
        info@morvane.com<br>
        www.morvane.com
      </p>
    </section>

    <svg class="corner-frame corner-frame--bottom-right" viewBox="0 0 230 212" role="img" aria-label="Scrolled corner ornament">
      <polygon class="corner-frame__fill" points="220,22 220,202 30,202"/>
      <polygon class="corner-frame__line" points="228,2 228,210 2,210"/>
      <polygon class="corner-frame__line" points="220,22 220,202 30,202"/>
    </svg>
  </main>
</body>
</html>
```